Website for International Non-Profit for Birth Parent Searching

LumaKin is a 501(c)(3) non-profit organization that helps Chinese adoptees search and reunite with birth families who were separated due the One Child Policy in China. We want to create a website that can link to an information database that allows website users to easily access information around search ads in an organized way; help connect families to professional searchers; provide resources for community support for adoptees and their families as they embark on a personal and emotional journey of finding birth family through support groups on social media and consultation/education on the searching process; and provide the opportunity for the adoptive community to give back through donations and volunteer opportunities. The final design should foster a sense of community and be easy navigable to access the multiple resources we provide to help families search for each other. We would like to see designs with red/black/white color schemes that are gentle, inviting, and family friendly to viewers. We would like to see some design layouts with Chinese themes, if possible.

```html
<!DOCTYPE html>
<html lang="en">
<head>
<meta charset="utf-8">
<title>LumaKin – Birth Family Search</title>
<link rel="stylesheet" href="https://fonts.googleapis.com/css2?family=Teko:wght@400;500&family=Open+Sans:wght@400;600&family=Arimo&display=swap">
<style>
:root{
  --red:#c8090d;
  --red-deep:#b30a0e;
  --cream:#f4ede0;
  --ink:#222;
  --muted:#8c8a85;
  --card:#5a5a5a;
  --bar:#2f2f2f;
  --white:#fff;
}
*{margin:0;padding:0;box-sizing:border-box}
html,body{width:1200px;height:4598px;overflow:hidden;background:var(--cream)}
body{font-family:"Open Sans",sans-serif;color:var(--ink);position:relative}
.abs{position:absolute}
.display{font-family:"Teko",sans-serif;font-weight:500;letter-spacing:.3px;text-transform:uppercase}
.btn{position:absolute;display:flex;align-items:center;justify-content:center;border-radius:26px;color:var(--white);font-family:"Teko",sans-serif;font-size:21px;text-transform:uppercase;padding-top:3px}
.photo{position:absolute}

/* header */
.site-header{left:0;top:0;width:1200px;height:77px;background:var(--cream)}
.brand{left:111px;top:14px;font-size:42px;color:var(--red)}
.nav{right:110px;top:32px;display:flex;gap:34px;font-family:"Arimo",sans-serif;font-size:15px;color:#333}
.nav .active{color:var(--red)}

/* hero */
.hero{left:0;top:77px;width:1200px;height:771px;background:linear-gradient(160deg,#7f8a3c 0%,#a9a459 35%,#6f6a42 60%,#4a4b34 100%)}
.hero-arrow{width:50px;height:50px;border-radius:50%;border:1.5px solid rgba(255,255,255,.7);top:429px}
.hero-panel{left:152px;top:550px;width:896px;height:239px;background:rgba(40,40,40,.45)}
.hero-title{left:0;top:564px;width:1200px;text-align:center;color:var(--white);font-size:80px;line-height:1}
.hero-text{left:230px;top:646px;width:740px;text-align:center;color:var(--white);font-size:14.5px;line-height:34px}

/* about */
.about-title{right:114px;top:945px;font-size:48px;color:var(--red)}
.about-text{left:375px;top:1014px;width:716px;text-align:right;font-size:14.5px;line-height:33.5px;color:var(--muted)}
.decor{left:0;top:848px;width:1200px;height:465px;background:linear-gradient(180deg,rgba(230,218,195,.5),rgba(244,237,224,0) 40%,rgba(225,215,195,.6))}

/* feature band */
.band-photo{left:0;top:1313px;width:1200px;height:589px;background:linear-gradient(180deg,#8a9aa6 0%,#a4aab0 45%,#6d7a5a 70%,#4d6b2a 100%)}
.frame{border:1.5px solid #444}
.red-box{background:var(--red)}
.feature-frame{left:43px;top:1238px;width:547px;height:414px}
.feature-box{left:50px;top:1245px;width:536px;height:403px}
.feature-title{left:75px;top:1310px;width:500px;font-size:30px;line-height:45px;color:var(--white);letter-spacing:0}
.feature-text{left:75px;top:1405px;width:480px;font-size:14.5px;line-height:32.5px;color:var(--white)}

/* services */
.section-title{left:0;width:1200px;text-align:center;font-size:48px;color:var(--red)}
.services-sub{left:180px;top:2050px;width:840px;text-align:center;font-size:14.5px;line-height:28px;color:var(--muted)}
.service{position:absolute;top:2138px;width:318px}
.service .photo{position:relative;height:255px;box-shadow:0 0 6px rgba(0,0,0,.15)}
.service h3{margin-top:26px;font-size:21px;font-weight:400;color:#333}
.service p{margin-top:4px;font-size:13px;line-height:28px;color:var(--muted)}
.link{display:inline-block;margin:12px 0 0 5px;font-family:"Teko",sans-serif;font-size:18px;color:var(--red);text-decoration:underline;text-transform:uppercase}

/* organized */
.org-photo{left:0;top:2674px;width:1200px;height:591px;background:linear-gradient(120deg,#b29a7a 0%,#8e6f55 35%,#c7a987 60%,#7b5a3c 100%)}
.org-frame{left:611px;top:2943px;width:546px;height:414px}
.org-box{left:618px;top:2950px;width:532px;height:403px}
.org-title{left:642px;top:2998px;font-size:48px;color:var(--white)}
.org-list{left:645px;top:3079px;width:440px;list-style:none;color:var(--white);font-size:13px;line-height:26.5px}
.org-list li{position:relative;padding-left:24px;margin-bottom:22px}
.org-list svg{position:absolute;left:0;top:6px}

/* blogs */
.kicker{left:0;top:3460px;width:1200px;text-align:center;font-size:24px;font-family:"Teko",sans-serif;color:#333}
.blog{position:absolute;top:3554px;width:318px;height:479px;background:var(--card);padding:5px}
.blog .photo{position:relative;height:268px}
.blog h3{margin:16px 0 0 7px;font-size:21px;font-weight:400;color:var(--white)}
.blog .rule{width:44px;height:2px;background:#ddd;margin:8px 0 0 7px}
.blog .date{margin:14px 0 0 7px;font-size:12.5px;color:var(--white);display:flex;align-items:center;gap:7px}
.blog p{margin:14px 7px 0 7px;font-size:12.5px;line-height:26px;color:#e6e6e6}
.blog p u{color:#f2f2f2}
.dots{left:536px;top:4077px;display:flex;gap:9px}
.dots span{width:25px;height:3px;background:#4a6a9a}
.dots .on{background:var(--red)}

/* footer */
.footer{left:0;top:4183px;width:1200px;height:362px;background:var(--red)}
.f-head{font-family:"Teko",sans-serif;font-size:18px;color:var(--white);text-transform:uppercase;position:absolute;top:4252px}
.f-text{position:absolute;color:var(--white);font-size:13px;line-height:29px}
.thumbs{left:788px;top:4299px;display:grid;grid-template-columns:repeat(3,100px);grid-auto-rows:89px;gap:5px}
.thumbs div{display:flex;align-items:center;justify-content:center;font-family:"Teko",sans-serif;font-size:18px;color:var(--white);text-decoration:underline}
.bottom-bar{left:0;top:4545px;width:1200px;height:53px;background:var(--bar)}
.b-nav{left:110px;top:4562px;display:flex;gap:33px;font-family:"Arimo",sans-serif;font-size:15px;color:var(--white)}
.social{left:886px;top:4548px;display:flex;gap:3px}
.social span{width:48px;height:46px;background:var(--white);display:flex;align-items:center;justify-content:center}
.social i{width:12px;height:12px;border-radius:50%;background:var(--bar)}
</style>
</head>
<body>

<header class="abs site-header">
  <div class="abs brand display">LumaKin</div>
  <nav class="abs nav">
    <span class="active">HOME</span><span>ABOUT</span><span>SERVICES</span><span>NEWS</span><span>FAQ</span><span>CONTACT</span><span>ENG ˅</span>
  </nav>
</header>

<section>
  <div class="abs hero" role="img" aria-label="Photo of a smiling family of three sitting together on grass in a sunny park"></div>
  <div class="abs hero-arrow" style="left:59px"><svg width="50" height="50"><path d="M27 20l-5 5 5 5" fill="none" stroke="#fff" stroke-width="1.5"/></svg></div>
  <div class="abs hero-arrow" style="left:1091px"><svg width="50" height="50"><path d="M23 20l5 5-5 5" fill="none" stroke="#fff" stroke-width="1.5"/></svg></div>
  <div class="abs hero-panel"></div>
  <h1 class="abs hero-title display">LumaKin</h1>
  <p class="abs hero-text">Lorem ipsum dolor sit amet, consectetur adipiscing elit, sed do eiusmod tempor incididunt ut labore et dolore magna aliqua. Ut enim ad minim veniam</p>
  <a class="btn" style="left:523px;top:716px;width:154px;height:48px;background:var(--red)">Donate now</a>
</section>

<section>
  <div class="abs decor" role="img" aria-label="Faint bamboo and mountain ink-wash backdrop"></div>
  <h2 class="abs about-title display">About us</h2>
  <p class="abs about-text">Lorem ipsum dolor sit amet, consectetur adipiscing elit, sed do eiusmod tempor incididunt ut labore et dolore magna aliqua. Ut enim ad minim veniam, quis nostrud exercitation ullamco laboris nisi ut aliquip ex ea commodo consequat. Duis aute irure dolor in reprehenderit in voluptate velit esse cillum dolore eu fugiat nulla pariatur. Excepteur sint occaecat cupidatat non proident, sunt in culpa qui officia deserunt mollit anim id est laborum</p>
  <a class="btn" style="left:111px;top:1064px;width:153px;height:50px;background:var(--red)">Read more</a>
</section>

<section>
  <div class="abs band-photo" role="img" aria-label="Photo of a family running and playing together on a lawn by the harbour"></div>
  <div class="abs frame feature-frame"></div>
  <div class="abs red-box feature-box"></div>
  <h2 class="abs feature-title display">Lorem ipsum dolor sit amet, consectetur<br>adipiscing elit,</h2>
  <p class="abs feature-text">Lorem ipsum dolor sit amet, consectetur adipiscing elit, sed do eiusmod tempor incididunt ut labore et dolore magna aliqua. Ut enim ad minim veniam, quis nostrud exercitation</p>
  <a class="btn" style="left:73px;top:1527px;width:154px;height:48px;background:#111">Get started</a>
</section>

<section>
  <h2 class="abs section-title display" style="top:1985px">Our services</h2>
  <p class="abs services-sub">Lorem ipsum dolor sit amet, consectetur adipiscing elit, sed do eiusmod tempor incididunt ut labore et dolore magna aliqua. Ut enim ad minim veniam, quis nostrud exercitation ullamco laboris</p>
  <article class="service" style="left:111px">
    <div class="photo" style="background:linear-gradient(135deg,#3b3f46,#7d8f5a 60%,#9bb56a)" role="img" aria-label="Photo of a father and two daughters sitting in the back of a car"></div>
    <h3 class="display" style="font-weight:400">Lorem ipsum dolor sit amet</h3>
    <p>Lorem ipsum dolor sit amet,adipiscing elit, sed do eiusmod tempor incididunt ut labore et dolore magna</p>
    <a class="link">Learn more</a>
  </article>
  <article class="service" style="left:441px">
    <div class="photo" style="background:linear-gradient(135deg,#e9e4da,#cfc7b6 55%,#b9ad8e)" role="img" aria-label="Photo of an elderly couple reading a book together on a sofa"></div>
    <h3 class="display" style="font-weight:400">Lorem ipsum dolor sit amet</h3>
    <p>Lorem ipsum dolor sit amet,adipiscing elit, sed do eiusmod tempor incididunt ut labore et dolore magna</p>
    <a class="link">Learn more</a>
  </article>
  <article class="service" style="left:770px">
    <div class="photo" style="background:linear-gradient(135deg,#d8cda5,#a79a73 55%,#6a6a52)" role="img" aria-label="Photo of grandparents talking with their grandson outdoors"></div>
    <h3 class="display" style="font-weight:400">Lorem ipsum dolor sit amet</h3>
    <p>Lorem ipsum dolor sit amet,adipiscing elit, sed do eiusmod tempor incididunt ut labore et dolore magna</p>
    <a class="link">Learn more</a>
  </article>
</section>

<section>
  <div class="abs org-photo" role="img" aria-label="Photo of a mother and daughter throwing autumn leaves into the air"></div>
  <div class="abs frame org-frame"></div>
  <div class="abs red-box org-box"></div>
  <h2 class="abs org-title display">Organized way</h2>
  <ul class="abs org-list">
    <li><svg width="13" height="13"><circle cx="6.5" cy="6.5" r="5.5" fill="none" stroke="#fff" stroke-width="1.5"/><circle cx="6.5" cy="6.5" r="2" fill="#fff"/></svg>Help connect families to professional searchers</li>
    <li><svg width="13" height="13"><circle cx="6.5" cy="6.5" r="5.5" fill="none" stroke="#fff" stroke-width="1.5"/><circle cx="6.5" cy="6.5" r="2" fill="#fff"/></svg>Provide resources for community support for adoptees and their families as they embark on a personal and emotional journey of finding birth family through support groups on social media and consultation/education on the searching process</li>
    <li><svg width="13" height="13"><circle cx="6.5" cy="6.5" r="5.5" fill="none" stroke="#fff" stroke-width="1.5"/><circle cx="6.5" cy="6.5" r="2" fill="#fff"/></svg>And provide the opportunity for the adoptive community to give back through donations and volunteer opportunities</li>
  </ul>
</section>

<section>
  <div class="abs kicker">NEWS</div>
  <h2 class="abs section-title display" style="top:3494px">Latest blogs</h2>
  <article class="blog" style="left:111px">
    <div class="photo" style="background:linear-gradient(135deg,#3d4a2a,#6b7b46 55%,#a09a7a)" role="img" aria-label="Photo of a father and children playing with water guns in a garden"></div>
    <h3 class="display" style="font-weight:400">Lorem ipsum dolor sit amet</h3><div class="rule"></div>
    <div class="date"><svg width="11" height="11"><rect x=".5" y="1.5" width="10" height="9" fill="none" stroke="#fff"/><path d="M.5 4.5h10" stroke="#fff"/></svg>january 15-01-2021</div>
    <p>Lorem ipsum dolor sit amet, r adipiscing elit, sed do eiusmod tempor incididunt utdolore magna aliqua. Ut enim ad minim veniam, READ MORE</p>
  </article>
  <article class="blog" style="left:441px">
    <div class="photo" style="background:linear-gradient(135deg,#5a4a40,#c4693a 50%,#d8c0a0)" role="img" aria-label="Photo of a multigenerational family sharing a festive meal"></div>
    <h3 class="display" style="font-weight:400">Lorem ipsum dolor sit amet</h3><div class="rule"></div>
    <div class="date"><svg width="11" height="11"><rect x=".5" y="1.5" width="10" height="9" fill="none" stroke="#fff"/><path d="M.5 4.5h10" stroke="#fff"/></svg>january 15-01-2021</div>
    <p>Lorem ipsum dolor sit amet, r adipiscing elit, sed do eiusmod tempor incididunt utdolore magna aliqua. Ut enim ad minim veniam, <u>READ MORE</u></p>
  </article>
  <article class="blog" style="left:770px">
    <div class="photo" style="background:linear-gradient(135deg,#4f6a3a,#8aa060 50%,#c9c3b0)" role="img" aria-label="Photo of a family riding bicycles along a country path"></div>
    <h3 class="display" style="font-weight:400">Lorem ipsum dolor sit amet</h3><div class="rule"></div>
    <div class="date"><svg width="11" height="11"><rect x=".5" y="1.5" width="10" height="9" fill="none" stroke="#fff"/><path d="M.5 4.5h10" stroke="#fff"/></svg>january 15-01-2021</div>
    <p>Lorem ipsum dolor sit amet, r adipiscing elit, sed do eiusmod tempor incididunt utdolore magna aliqua. Ut enim ad minim veniam, <u>READ MORE</u></p>
  </article>
  <div class="abs dots"><span></span><span class="on"></span><span></span><span></span></div>
</section>

<footer>
  <div class="abs footer"></div>
  <div class="f-head" style="left:96px">About us</div>
  <p class="f-text" style="left:96px;top:4296px;width:360px;font-size:12px;line-height:28.5px">Lorem ipsum dolor sit amet, consectetur adipiscing elit, sed do eiusmod tempor incididunt ut labore et dolore magna aliqua. Ut enim ad minim veniam, quis nostrud exercitation ullamco laboris nisi ut aliquip</p>
  <p class="f-text" style="left:96px;top:4463px;font-size:13px">© 2021 All Rights Reserved</p>
  <div class="f-head" style="left:498px">Contact</div>
  <div class="f-text" style="left:498px;top:4291px;width:240px">
    <div><svg width="11" height="11"><path d="M2 1l3 0 1 3-2 1c1 2 2 3 4 4l1-2 3 1v3c-6 0-10-4-10-10z" fill="#fff"/></svg> 555-014-2290</div>
    <div style="margin-top:6px"><svg width="12" height="10"><rect width="12" height="10" fill="#fff"/><path d="M0 0l6 5 6-5" fill="none" stroke="#c8090d"/></svg> info@lumakin.org</div>
    <div style="margin-top:6px"><svg width="9" height="12"><path d="M4.5 0a4.5 4.5 0 0 1 4.5 4.5c0 3-4.5 7.5-4.5 7.5S0 7.5 0 4.5A4.5 4.5 0 0 1 4.5 0z" fill="#fff"/><circle cx="4.5" cy="4.5" r="1.6" fill="#c8090d"/></svg> Lorem ipsum dolor sit amet, consectetu</div>
  </div>
  <div class="f-head" style="left:786px">News</div>
  <div class="abs thumbs">
    <div style="background:#9aa8b0" role="img" aria-label="Thumbnail of a family walking outdoors"></div>
    <div style="background:#d9b9a6" role="img" aria-label="Thumbnail of a mother with her child"></div>
    <div style="background:#7a6a5a" role="img" aria-label="Thumbnail of a family portrait"></div>
    <div style="background:#c9b8a8" role="img" aria-label="Thumbnail of a family gathering"></div>
    <div style="background:#8a6d60">READ MORE</div>
    <div style="background:#b59a8a" role="img" aria-label="Thumbnail of smiling relatives together"></div>
  </div>
  <div class="abs bottom-bar"></div>
  <nav class="abs b-nav"><span>HOME</span><span>ABOUT</span><span>SERVICES</span><span>NEWS</span><span>FAQ</span><span>CONTACT</span></nav>
  <div class="abs social"><span><i></i></span><span><i></i></span><span><i></i></span><span><i></i></span></div>
</footer>

</body>
</html>
```